Custom unique Stationary design for Logistics company

We need a custom, unique , elegant and luxurious full stationary design using our new logo, following these guidelines:
1- Business card: double sided, both sides uses the navy blue as the background main color (same as the code of the navy blue used in our logo).
2- envelope and folder: also use the same navy blue as the main background color.
3- book cover( notepad cover) : same thing with the navy blue
4- letterhead: feel free to use the combination of the colors in our logo.
5- rest of the items are up to your creativity

Target Market(s)

corporates and other businesses

Industry/Entity Type

Logistics and heavy machines contractors

Requirements
Must have
• Letterhead, business card, envelope, notepad cover, paper, file
Nice to have
• navy blue to be main background color for business card, envelope, notepad cover

```html
<!DOCTYPE html>
<html lang="en">
<head>
<meta charset="utf-8">
<title>Northline Freight Group – Business Card</title>
<link href="https://fonts.googleapis.com/css2?family=Saira:wght@300;400;700;800&display=swap" rel="stylesheet">
<style>
  :root {
    --navy: #005078;
    --orange: #f05a28;
    --white: #ffffff;
    --ink: #3f3f3f;
    --muted: #a9bccb;
    --glow: #12d8f5;
    --backdrop: #dcdcdc;
  }
  * { margin: 0; padding: 0; box-sizing: border-box; }
  html, body { width: 1200px; height: 1200px; overflow: hidden; }
  body {
    background: var(--backdrop);
    font-family: "Saira", "Segoe UI", sans-serif;
    position: relative;
  }
  .card {
    position: absolute;
    left: 262px;
    width: 684px;
    height: 391px;
    border-radius: 21px;
    overflow: hidden;
  }
  .card--front { top: 165px; background: var(--white); }
  .card--back { top: 653px; background: var(--navy); }

  .card__art { position: absolute; inset: 0; width: 100%; height: 100%; }

  .contact { position: absolute; left: 31px; top: 0; color: var(--ink); }
  .contact__name {
    position: absolute; top: 104px; white-space: nowrap;
    font-size: 23px; font-weight: 400; color: var(--orange); letter-spacing: 0.3px;
  }
  .contact__role {
    position: absolute; top: 134px; white-space: nowrap;
    font-size: 15px; font-weight: 400;
  }
  .contact__address {
    position: absolute; top: 162px; white-space: nowrap;
    font-size: 15.5px; font-weight: 300; line-height: 19px; font-style: normal;
    letter-spacing: 0.3px;
  }
  .contact__list { position: absolute; top: 210px; list-style: none; }
  .contact__item {
    display: flex; align-items: center; gap: 8px; white-space: nowrap;
    font-size: 14.5px; font-weight: 300; height: 19.5px; letter-spacing: 0.2px;
  }
  .contact__icon { width: 12px; height: 12px; flex: none; fill: var(--orange); }

  .brand { position: absolute; text-align: center; color: var(--white); }
  .brand--front { left: 386px; width: 260px; top: 150px; }
  .brand--back { left: 0; width: 684px; top: 22px; }
  .brand__name { font-weight: 800; line-height: 1; letter-spacing: 2px; }
  .brand--front .brand__name { font-size: 98px; }
  .brand--back .brand__name { font-size: 136px; }
  .brand__tagline {
    font-size: 11px; font-weight: 700; letter-spacing: 1.2px;
    color: var(--muted); margin-top: -6px; white-space: nowrap;
  }
  .brand__web {
    font-size: 15px; font-weight: 700; letter-spacing: 3.6px; margin-top: 6px;
  }

  .card__glow {
    position: absolute; left: 0; right: 0; bottom: 0; height: 150px;
    background: radial-gradient(ellipse 70% 100% at 45% 100%, rgba(18,216,245,0.55) 0%, rgba(18,160,230,0.25) 45%, rgba(0,80,120,0) 75%);
  }
</style>
</head>
<body>

<section class="card card--front" aria-label="Business card front">
  <svg class="card__art" viewBox="0 0 798 456" preserveAspectRatio="none" aria-hidden="true">
    <path fill="var(--navy)" d="M474 0 C340 100 320 290 442 412 L477 456 L798 456 L798 0 Z"/>
    <path fill="none" stroke="var(--white)" stroke-width="3" d="M508 0 C380 90 330 270 468 448"/>
    <path fill="var(--orange)" d="M511 0 C383 90 333 270 471 448 L477 456 L798 456 L798 0 Z"/>
    <path fill="var(--navy)" d="M502 0 C390 110 370 300 514 456 L798 456 L798 0 Z"/>
  </svg>

  <div class="contact">
    <h1 class="contact__name">DANIEL HARPER</h1>
    <p class="contact__role">President</p>
    <address class="contact__address">1420 Cedar Ridge Road<br>Juneau, Alaska 34611</address>
    <ul class="contact__list">
      <li class="contact__item">
        <svg class="contact__icon" viewBox="0 0 12 12"><path d="M2.4 0.6 L4.4 2.8 L3.4 4.2 C4 5.6 6.2 7.8 7.8 8.6 L9.2 7.6 L11.4 9.6 L10 11.4 C5.6 11.2 0.8 6.4 0.6 2 Z"/></svg>
        555-214-7730
      </li>
      <li class="contact__item">
        <svg class="contact__icon" viewBox="0 0 12 12"><path d="M3 0 H9 V12 H3 Z M4.2 1.4 V9 H7.8 V1.4 Z" fill-rule="evenodd"/></svg>
        555-618-0942
      </li>
      <li class="contact__item">
        <svg class="contact__icon" viewBox="0 0 12 12"><path d="M0 2.5 H12 V9.5 H0 Z"/><path d="M0.5 3 L6 6.8 L11.5 3" stroke="#fff" stroke-width="1" fill="none"/></svg>
        hello@northlinefreightgroup.com
      </li>
      <li class="contact__item">
        <svg class="contact__icon" viewBox="0 0 12 12"><circle cx="6" cy="6" r="6"/><path d="M1 6 H11 M6 1 C3.5 3.5 3.5 8.5 6 11 M6 1 C8.5 3.5 8.5 8.5 6 11" stroke="#fff" stroke-width="0.9" fill="none"/></svg>
        northlinefreightgroup.com
      </li>
    </ul>
  </div>

  <div class="brand brand--front">
    <p class="brand__name">NFG</p>
    <p class="brand__tagline">NORTHLINE FREIGHT GROUP</p>
  </div>
</section>

<section class="card card--back" aria-label="Business card back">
  <div class="brand brand--back">
    <p class="brand__name">NFG</p>
    <p class="brand__web">northlinefreightgroup.com</p>
  </div>
  <div class="card__glow" role="img" aria-label="Large decorative brand emblem in bright cyan fading to dark"></div>
</section>

</body>
</html>
```